English and Spanish Language School Needs a Business Card

Need a business card design a startup company called Maribel Language School. The company will offer English and Spanish conversational level courses designed to make the learner feel comfortable with grammar and vocabulary. We would like to see a logo with some colour that should communicate learning, growth.

Target Market(s)

Consumers and businesses

Industry/Entity Type

Education

Contact Information for Business Card

TBD

Font styles to use
Serif

Requirements
Must have
• Include the following
• Logo
• Name
• Title
• Cellphone Number
• Office Phone number
• Email address
• Office Address

```html
<!DOCTYPE html>
<html lang="en">
<head>
<meta charset="utf-8">
<title>Maribel Language School – Business Card</title>
<link href="https://fonts.googleapis.com/css2?family=Tinos:wght@400;700&display=swap" rel="stylesheet">
<style>
  :root {
    --bg: #e9e6e1;
    --paper: #ffffff;
    --paper-shade: #f1f1f1;
    --brand-red: #c4212f;
    --brand-red-dark: #a51a26;
    --brand-teal: #14b3b8;
    --ink: #7b7b7b;
    --ink-dark: #5a5a5a;
  }
  * { margin: 0; padding: 0; box-sizing: border-box; }
  html, body { width: 1200px; height: 780px; overflow: hidden; }
  body {
    background: var(--bg);
    font-family: "Tinos", "Times New Roman", serif;
    display: flex;
    align-items: center;
    justify-content: center;
    gap: 48px;
  }
  .card {
    position: relative;
    width: 536px;
    height: 306px;
    background: linear-gradient(135deg, var(--paper) 40%, var(--paper-shade));
    box-shadow: 0 10px 24px rgba(0,0,0,0.18);
    overflow: hidden;
  }
  .card__wave { position: absolute; inset: 0; width: 100%; height: 100%; }
  .brand {
    position: absolute;
    color: var(--brand-red);
    font-weight: 700;
    line-height: 1;
  }
  .brand__name { display: block; letter-spacing: -0.5px; }
  .brand__sub { display: block; margin-top: 4px; }

  .card--front .brand { top: 46px; left: 250px; }
  .card--front .brand__name { font-size: 58px; }
  .card--front .brand__sub { font-size: 19px; padding-left: 4px; }

  .person { position: absolute; left: 34px; top: 170px; }
  .person__name {
    color: var(--brand-red);
    font-size: 17px;
    font-weight: 400;
    text-transform: uppercase;
    letter-spacing: 0.3px;
  }
  .person__title { color: var(--ink-dark); font-size: 13px; margin-top: 1px; }

  .contact {
    position: absolute;
    left: 34px;
    top: 216px;
    list-style: none;
    color: var(--ink);
    font-size: 12.5px;
    line-height: 15px;
  }
  .contact__address { margin-bottom: 4px; }
  .contact__row { display: flex; align-items: center; gap: 6px; margin-bottom: 2px; }
  .contact__icon { width: 13px; height: 13px; flex: none; }

  .card--back .brand { top: 108px; left: 200px; }
  .card--back .brand__name { font-size: 72px; }
  .card--back .brand__sub { font-size: 22px; padding-left: 6px; }
</style>
</head>
<body>

<section class="card card--front" aria-label="Business card front">
  <svg class="card__wave" viewBox="0 0 536 306" preserveAspectRatio="none" aria-hidden="true">
    <path d="M200 306 C300 300 330 240 380 150 C420 80 470 20 536 10 L536 0 C455 12 405 70 360 150 C320 225 290 290 200 296 Z" fill="var(--brand-teal)"/>
    <path d="M236 306 C330 306 360 250 405 165 C440 95 485 40 536 32 L536 306 Z" fill="var(--brand-red)"/>
    <path d="M236 306 C330 306 360 250 405 165 C440 95 485 40 536 32 L536 50 C495 60 455 110 420 180 C380 260 350 306 280 306 Z" fill="var(--brand-red-dark)" opacity="0.35"/>
  </svg>

  <div class="brand">
    <span class="brand__name">Maribel</span>
    <span class="brand__sub">Language School</span>
  </div>

  <div class="person">
    <h1 class="person__name">Daniel Reyes</h1>
    <p class="person__title">Manager</p>
  </div>

  <ul class="contact">
    <li class="contact__address">48 Alder Lane, Suite 2<br>Elmbrook, Texas 7730</li>
    <li class="contact__row">
      <svg class="contact__icon" viewBox="0 0 13 13" aria-label="Office phone"><rect width="13" height="13" fill="var(--brand-red)"/><path d="M3 4 Q3 3 4 3 L9 3 Q10 3 10 4 L10 5 L8 5 L8 4 L5 4 L5 5 L3 5 Z M4 6 L9 6 L10 10 L3 10 Z" fill="#fff"/></svg>
      <span>555 214 3680</span>
    </li>
    <li class="contact__row">
      <svg class="contact__icon" viewBox="0 0 13 13" aria-label="Mobile phone"><rect width="13" height="13" fill="var(--brand-red)"/><rect x="4.5" y="2" width="4" height="9" rx="0.8" fill="#fff"/><rect x="5.3" y="3" width="2.4" height="5" fill="var(--brand-red)"/></svg>
      <span>555 214 3681</span>
    </li>
    <li class="contact__row">
      <svg class="contact__icon" viewBox="0 0 13 13" aria-label="Email"><rect width="13" height="13" fill="var(--brand-red)"/><rect x="2.5" y="4" width="8" height="5.5" fill="#fff"/><path d="M2.5 4 L6.5 7 L10.5 4" stroke="var(--brand-red)" stroke-width="0.9" fill="none"/></svg>
      <span>hello@maribelschool.com</span>
    </li>
  </ul>
</section>

<section class="card card--back" aria-label="Business card back">
  <svg class="card__wave" viewBox="0 0 536 306" preserveAspectRatio="none" aria-hidden="true">
    <path d="M0 70 C60 70 90 120 125 190 C155 250 185 300 250 306 L236 306 C170 300 140 250 112 195 C80 130 55 85 0 82 Z" fill="var(--brand-teal)"/>
    <path d="M0 95 C50 100 80 140 108 200 C135 260 160 300 212 306 L0 306 Z" fill="var(--brand-red)"/>
    <path d="M0 120 C40 125 70 160 95 215 C120 270 140 300 180 306 L0 306 Z" fill="var(--brand-red-dark)" opacity="0.35"/>
  </svg>

  <div class="brand">
    <span class="brand__name">Maribel</span>
    <span class="brand__sub">Language School</span>
  </div>
</section>

</body>
</html>
```